Website for "Bright Morrow Ltd" cleaning bsuiness

We require a website to expose our business to the local market. We want to provide background on who we are and what we do but in an easily digestible way. We clean domestic and commercial premises and want to provide a list of all of our services to potential customers. We operate out of Warrington in the UK.

We would like the website to be animated in some way so that the experience of using it is not dull or mundane. This website needs to be an extension of our company.

Target Market(s)

30 - 60 year olds for Domestic plus commercial clients

Industry/Entity Type

Cleaning Service

Coding

Coded - Design and coding required

Number of Pages Required

4 page

Font styles to use
Sans Serif

Colors
0455a3
3176b5
85acd3
cfdeed
ffffff
000000
1b1b1b
c8c8c8
757575

Requirements
Must have
• Logo which has been provided. Theme based around the logo and its colours. Simple layout to avoid confusion.
Nice to have
• Animations where possible to impress the customer.
Should not have
• any pictures of cleaning equipment, fairies, maids etc

```html
<!DOCTYPE html>
<html lang="en">
<head>
<meta charset="utf-8">
<title>Bright Morrow Ltd – Professional Cleaning Services</title>
<link rel="stylesheet" href="https://fonts.googleapis.com/css2?family=Raleway:wght@300;400;500;600&family=Great+Vibes&display=swap">
<style>
:root{
  --brand:#0455a3;
  --brand-mid:#3176b5;
  --brand-soft:#85acd3;
  --brand-pale:#cfdeed;
  --white:#ffffff;
  --ink:#1b1b1b;
  --grey:#757575;
  --line:#c8c8c8;
}
*{box-sizing:border-box;margin:0;padding:0}
html,body{width:1200px;height:2748px;overflow:hidden;background:var(--white)}
body{position:relative;font-family:Arial,Helvetica,sans-serif;color:var(--grey)}
.abs{position:absolute}
.raleway{font-family:Raleway,Arial,sans-serif}
.script{font-family:"Great Vibes",cursive}
.btn{position:absolute;display:flex;align-items:center;justify-content:center;border-radius:30px;font-family:Raleway,Arial,sans-serif;font-weight:500;font-size:22px;color:var(--white);background:var(--brand);text-transform:uppercase;text-decoration:none}
.btn.outline{background:transparent;border:2px solid var(--white)}

/* top bar */
.topbar{left:0;top:0;width:1200px;height:48px;background:var(--brand)}
.topbar .social{left:76px;top:17px;display:flex;gap:16px}
.topbar .social span{width:14px;height:14px;border-radius:50%;background:var(--brand-pale);display:block}
.topbar .contact{right:78px;top:0;height:48px;display:flex;align-items:center;gap:40px;color:var(--white);font-size:16px}
.topbar .contact .mail{color:var(--brand-pale)}
.topbar .contact div{display:flex;align-items:center;gap:10px}

/* nav */
.nav{left:0;top:48px;width:1200px;height:98px;background:var(--white)}
.nav a{position:absolute;top:38px;font-family:Raleway,Arial,sans-serif;font-size:18px;color:var(--ink);text-decoration:none;text-transform:uppercase}
.nav a.active{top:26px;left:103px;width:94px;height:44px;border-radius:24px;background:var(--brand);color:var(--white);display:flex;align-items:center;justify-content:center}
.brand{left:500px;top:64px;width:200px;display:flex;flex-direction:column;align-items:center;gap:8px;text-align:center}
.brand .dot{width:24px;height:24px;border-radius:50%;background:var(--brand)}
.brand .name{font-family:Raleway,Arial,sans-serif;font-weight:600;font-size:22px;color:var(--brand);line-height:1.1;white-space:nowrap}

/* hero */
.hero{left:0;top:146px;width:1200px;height:521px;background:linear-gradient(135deg,#c9ae83 0%,#d9c3a0 45%,#bfa078 100%)}
.hero-title{right:78px;top:312px;font-family:Raleway,Arial,sans-serif;font-weight:300;font-size:64px;line-height:1;color:var(--white)}
.hero-sub{right:78px;top:394px;font-size:32px;line-height:1;color:var(--white)}
.hero .arrow{top:243px;width:52px;height:52px;border:2px solid #3c3c3c;border-radius:50%;display:flex;align-items:center;justify-content:center}

/* welcome */
.h-section{font-family:Raleway,Arial,sans-serif;font-weight:400;font-size:42px;line-height:1.1;color:var(--ink);text-transform:uppercase;letter-spacing:.5px}
.h-section em{font-style:normal;color:var(--brand)}
.body-copy{font-size:14px;line-height:27px;color:var(--grey)}
.welcome-img{left:792px;top:738px;width:331px;height:246px;background:linear-gradient(160deg,#eef0f1,#c9ced3 70%,#9aa4ad)}

/* services */
.services{left:0;top:1081px;width:1200px;height:500px;background:var(--brand-soft)}
.svc-sub{font-family:"Great Vibes",cursive;font-size:25px;line-height:1;color:var(--ink)}
.svc-list{list-style:none;font-size:15px;color:var(--white);line-height:29px}
.svc-list li{display:flex;align-items:center;gap:18px}
.svc-list.right li{justify-content:flex-end}
.star{color:var(--white);font-size:12px}
.svc-head{font-family:Raleway,Arial,sans-serif;font-size:19px;color:var(--brand)}
.vacuum{left:556px;top:1152px;width:200px;height:412px;border-radius:28px;background:linear-gradient(170deg,#3b4f73 0%,#2a5fb8 45%,#1c3e7a 100%)}

/* cta band */
.cta-band{left:0;top:1581px;width:1200px;height:156px;background:var(--brand)}

/* what we do */
.tile{position:absolute;width:249px;height:175px;border:6px solid var(--brand-soft)}

/* footer */
.footer{left:0;top:2422px;width:1200px;height:264px;background:var(--brand)}
.footer h4{font-family:Raleway,Arial,sans-serif;font-weight:600;font-size:18px;color:var(--brand-soft);text-transform:uppercase;letter-spacing:.5px}
.footer ul{list-style:none;color:var(--white);font-size:14px;line-height:27px}
.footer ul li::before{content:"";display:inline-block;width:7px;height:7px;border:1px solid var(--white);margin-right:14px;vertical-align:middle}
.f-text{color:var(--white);font-size:14px;line-height:24px}
.copyright{left:0;top:2686px;width:1200px;height:62px;background:var(--brand-soft);display:flex;align-items:center;justify-content:center;font-size:14px;color:var(--white)}
.copyright b{color:var(--brand);font-weight:400;margin:0 6px}
</style>
</head>
<body>

<header>
  <div class="abs topbar">
    <div class="abs social"><span></span><span></span><span></span></div>
    <div class="abs contact">
      <div><svg width="16" height="16" viewBox="0 0 24 24"><path fill="#fff" d="M6.6 10.8a15.1 15.1 0 0 0 6.6 6.6l2.2-2.2c.3-.3.7-.4 1-.2 1.1.4 2.3.6 3.6.6.6 0 1 .4 1 1V20c0 .6-.4 1-1 1A17 17 0 0 1 3 4c0-.6.4-1 1-1h3.5c.6 0 1 .4 1 1 0 1.3.2 2.5.6 3.6.1.3 0 .7-.2 1z"/></svg>01925 555 0142</div>
      <div class="mail"><svg width="18" height="14" viewBox="0 0 18 14"><rect x="1" y="1" width="16" height="12" fill="none" stroke="#cfdeed" stroke-width="1.5"/><path d="M1 1l8 7 8-7" fill="none" stroke="#cfdeed" stroke-width="1.5"/></svg>info@brightmorrow.example</div>
    </div>
  </div>

  <nav class="abs nav">
    <a class="active" href="#">Home</a>
    <a href="#" style="left:234px">About Us</a>
    <a href="#" style="left:372px">Services</a>
    <a href="#" style="left:748px">Blog</a>
    <a href="#" style="left:861px">Contact Us</a>
    <svg class="abs" style="left:1098px;top:40px" width="24" height="24" viewBox="0 0 24 24"><circle cx="10" cy="10" r="7" fill="none" stroke="#0455a3" stroke-width="3"/><path d="M15 15l6 6" stroke="#0455a3" stroke-width="3.5" stroke-linecap="round"/></svg>
  </nav>
  <div class="abs brand"><span class="dot"></span><span class="name">Bright Morrow Ltd</span></div>
</header>

<section class="abs hero" role="img" aria-label="Photo of a tiled floor being steam cleaned">
  <div class="abs arrow" style="left:14px"><svg width="16" height="16" viewBox="0 0 16 16"><path d="M11 2L5 8l6 6" fill="none" stroke="#3c3c3c" stroke-width="2"/></svg></div>
  <div class="abs arrow" style="right:14px"><svg width="16" height="16" viewBox="0 0 16 16"><path d="M5 2l6 6-6 6" fill="none" stroke="#3c3c3c" stroke-width="2"/></svg></div>
</section>
<h1 class="abs hero-title">Bright Morrow</h1>
<p class="abs hero-sub script">Professional Cleaning Services</p>
<a class="btn" style="left:933px;top:444px;width:190px;height:56px">Contact Us</a>

<section>
  <h2 class="abs h-section" style="left:79px;top:724px">Welcome to <em>Bright Morrow</em></h2>
  <div class="abs body-copy" style="left:79px;top:786px;width:680px">
    <p>Lorem Ipsum is simply dummy text of the printing and typesetting industry. Lorem Ipsum has been the industry's standard dummy text ever since the 1500s, when an unknown printer took a galley of type and scrambled it to make a type specimen book.It has survived not only five centuries. Lorem Ipsum is simply dummy text of the printing and typesetting industry.</p>
    <p>Lorem Ipsum is simply dummy text of the printing and typesetting industry. Lorem Ipsum has been the industry's standard dummy text ever since the 1500s, when an unknown printer took.</p>
  </div>
  <a class="btn" style="left:79px;top:962px;width:189px;height:56px">Know More</a>
  <div class="abs welcome-img" role="img" aria-label="Photo of a bright, clean living room"></div>
</section>

<section class="abs services"></section>
<div class="abs vacuum" role="img" aria-label="Product photo of a canister vacuum cleaner"></div>
<h2 class="abs h-section" style="left:79px;top:1142px">Domestic <em>Services</em></h2>
<p class="abs svc-sub" style="left:81px;top:1198px">Weekly, fortnightly, monthly and adhoc cleans available</p>
<div class="abs" style="left:81px;top:1243px">
  <div class="svc-head" style="display:flex;gap:18px;align-items:center"><span class="star" style="color:var(--brand)">✳</span>Ironing</div>
  <p class="body-copy" style="color:var(--white);margin:4px 0 0 32px;width:430px">Lorem Ipsum is simply dummy text of the printing and typesetting industry. Lorem Ipsum has been the industry's standard.</p>
  <ul class="svc-list" style="margin-top:10px">
    <li><span class="star">✳</span>Carpet Cleaning</li>
    <li><span class="star">✳</span>Tiled floor steam clean</li>
    <li><span class="star">✳</span>End of tenancy clean</li>
    <li><span class="star">✳</span>New house pre moving in clean</li>
    <li><span class="star">✳</span>Emergency requested clean</li>
  </ul>
</div>
<h2 class="abs h-section" style="right:77px;top:1142px">Commercial <em>Cleaning</em></h2>
<p class="abs svc-sub" style="right:77px;top:1198px;font-size:22px">contract daily cleaning</p>
<div class="abs" style="right:77px;top:1241px;text-align:right">
  <div class="svc-head" style="display:flex;gap:18px;align-items:center;justify-content:flex-end">Vacuuming<span class="star" style="color:var(--brand)">✳</span></div>
  <p class="body-copy" style="color:var(--brand-pale);margin:4px 30px 0 auto;width:330px">Lorem Ipsum is simply dummy text of the printing and typesetting industry. Lorem Ipsum has been the industry's standard.</p>
  <ul class="svc-list right" style="margin-top:10px">
    <li>Desk polishing<span class="star">✳</span></li>
    <li>Bin emptying<span class="star">✳</span></li>
    <li>Toilet cleaning<span class="star">✳</span></li>
  </ul>
</div>

<section class="abs cta-band">
  <h3 class="abs raleway" style="left:79px;top:30px;font-weight:500;font-size:24px;color:var(--white);text-transform:uppercase">Bright Morrow</h3>
  <p class="abs body-copy" style="left:79px;top:70px;width:680px;color:var(--brand-pale)">Lorem Ipsum is simply dummy text of the printing and typesetting industry. Lorem Ipsum has been the industry's standard dummy text ever since the 1500s, when an unknown printer took.</p>
  <a class="btn outline" style="left:873px;top:51px;width:250px;height:56px">Contact Us Know</a>
</section>

<section>
  <h2 class="abs h-section" style="left:0;width:1200px;text-align:center;top:1790px">What <em>We Do</em></h2>
  <p class="abs body-copy" style="left:230px;top:1850px;width:740px;text-align:center">Lorem Ipsum is simply dummy text of the printing and typesetting industry. Lorem Ipsum has been the industry's standard dummy text ever since the when an unknown printer took a galley.</p>
  <div class="tile" style="left:79px;top:1920px;background:linear-gradient(160deg,#e58a4a,#6b3a22)" role="img" aria-label="Photo of a wooden floor being vacuumed"></div>
  <div class="tile" style="left:344px;top:1920px;background:linear-gradient(160deg,#f2f2f2,#c9c9c9)" role="img" aria-label="Photo of folded laundry beside an iron"></div>
  <div class="tile" style="left:609px;top:1920px;background:linear-gradient(160deg,#dfe7ea,#9fb2bb)" role="img" aria-label="Photo of tiles being cleaned with a hose"></div>
  <div class="tile" style="left:874px;top:1920px;background:linear-gradient(160deg,#f4e4cf,#c0895a)" role="img" aria-label="Photo of an empty room with moving boxes"></div>
  <div class="tile" style="left:79px;top:2112px;background:linear-gradient(160deg,#e9e9e9,#4a4a4a)" role="img" aria-label="Photo of a floor being mopped"></div>
  <div class="tile" style="left:344px;top:2112px;background:linear-gradient(160deg,#7a4a2a,#a86a3c)" role="img" aria-label="Photo of a wooden desk being polished"></div>
  <div class="tile" style="left:609px;top:2112px;background:linear-gradient(160deg,#3f4a2c,#7fa35a)" role="img" aria-label="Photo of a commercial bin trolley"></div>
  <div class="tile" style="left:874px;top:2112px;background:linear-gradient(160deg,#f5f5f3,#bfbcb6)" role="img" aria-label="Photo of a clean bathroom toilet"></div>
  <a class="btn" style="left:518px;top:2303px;width:165px;height:55px">View All</a>
</section>

<footer class="abs footer">
  <div class="abs" style="left:79px;top:32px">
    <h4>Usefull Links</h4>
    <ul style="margin-top:16px"><li>Home</li><li>About Us</li><li>Services</li><li>Blog</li><li>Contact Us</li></ul>
  </div>
  <div class="abs" style="left:335px;top:32px;width:240px">
    <h4>Get in Touch</h4>
    <div style="display:flex;gap:16px;margin-top:16px">
      <svg width="22" height="20" viewBox="0 0 22 20" style="flex:none;margin-top:4px"><path d="M1 3l6-2 8 2 6-2v16l-6 2-8-2-6 2z M7 1v16 M15 3v16" fill="none" stroke="#cfdeed" stroke-width="1.3"/></svg>
      <p class="f-text">101- Lorem ipsum is simple dummy text of print and type setting industry</p>
    </div>
    <div style="display:flex;gap:16px;margin-top:22px;align-items:center">
      <svg width="22" height="22" viewBox="0 0 24 24"><path d="M6.6 10.8a15.1 15.1 0 0 0 6.6 6.6l2.2-2.2c.3-.3.7-.4 1-.2 1.1.4 2.3.6 3.6.6.6 0 1 .4 1 1V20c0 .6-.4 1-1 1A17 17 0 0 1 3 4c0-.6.4-1 1-1h3.5c.6 0 1 .4 1 1 0 1.3.2 2.5.6 3.6.1.3 0 .7-.2 1z" fill="none" stroke="#cfdeed" stroke-width="1.3"/></svg>
      <span class="f-text">01925 555 0142</span>
    </div>
    <div style="display:flex;gap:16px;margin-top:22px;align-items:center">
      <svg width="22" height="16" viewBox="0 0 22 16"><rect x="1" y="1" width="20" height="14" fill="none" stroke="#cfdeed" stroke-width="1.3"/><path d="M1 1l10 8 10-8" fill="none" stroke="#cfdeed" stroke-width="1.3"/></svg>
      <span class="f-text">hello@brightmorrow.example</span>
    </div>
  </div>
  <div class="abs" style="left:601px;top:32px;width:250px">
    <h4>Newsletter</h4>
    <p class="f-text" style="margin-top:14px">Would you like to receive exclusive access to articles, white papers and our regular monthly newsletter?</p>
    <div style="margin-top:12px;width:249px;height:40px;background:var(--white);color:var(--grey);font-size:14px;padding:11px 12px">Enter Email Id</div>
    <div class="btn outline" style="position:relative;margin-top:12px;width:155px;height:42px;font-size:19px">Submit</div>
  </div>
  <div class="abs" style="left:883px;top:32px">
    <h4>Follow Us</h4>
    <div style="display:flex;gap:12px;margin-top:22px">
      <span style="width:46px;height:46px;border-radius:50%;background:var(--brand-soft)"></span>
      <span style="width:46px;height:46px;border-radius:50%;border:2px solid var(--brand-pale)"></span>
      <span style="width:46px;height:46px;border-radius:50%;border:2px solid var(--brand-pale)"></span>
    </div>
  </div>
</footer>
<div class="abs copyright">© 2016 <b>Bright Morrow</b> - All rights reserved.</div>

</body>
</html>
```